Podiatry clinic requires a modern revamp and editing of existing website.

I would like a fresh new look and updated information for my current business website. An easy to navigate site with prominent address and phone number for call to action. We are a podiatry clinic that focuses on general and sports podiatry.
I would like 4 pages; including Home page, About Us, Services & Contact.
www.brambleridgepodiatry.net

Target Market(s)

Active working professionals.

Industry/Entity Type

Medical

Coding

Coded - Design and coding required

Number of Pages Required

4 page

Font styles to use
Sans Serif

Colors
6b449b

Requirements
Must have
• A modern look with logo and active images; clean and uncluttered. Visible phone number and address for call to action.
• 4 pages - Home, About Us, Services, Contact.
• Home page - update address & service logos.
• About Us - update of personal information.
• Services - Revamp of existing page.
• Contact page to include Google map, email & phone number.
Nice to have
• Ability to add content easily; eg. a blog or adding video onto Home page.
• Link to Facebook page.

```html
<!DOCTYPE html>
<html lang="en">
<head>
<meta charset="utf-8">
<title>Brambleridge Podiatry</title>
<link href="https://fonts.googleapis.com/css2?family=Open+Sans:wght@400;600;700&display=swap" rel="stylesheet">
<style>
:root{
  --purple:#6b449b;
  --yellow:#f7c51e;
  --grey-dark:#4a4a4c;
  --grey-light:#eeeeee;
  --text:#444;
  --white:#fff;
}
*{box-sizing:border-box;margin:0;padding:0}
html,body{width:813px;height:1200px;overflow:hidden}
body{font-family:"Open Sans",sans-serif;color:var(--text);background:var(--white);position:relative}
.header{height:56px;display:flex;align-items:center;padding:0 52px;background:var(--white);position:relative;z-index:3}
.logo{display:flex;align-items:center;gap:6px;background:var(--purple);padding:6px 10px;height:44px}
.logo-mark{width:12px;height:12px;background:var(--yellow);flex:none}
.logo-name{color:var(--white);font-weight:700;font-size:12px;line-height:1.05;width:84px}
.nav{display:flex;gap:22px;margin-left:80px;font-size:10px}
.nav a{color:var(--text);text-decoration:none}
.nav a.active{color:var(--purple);font-weight:600}
.call{margin-left:auto;display:flex;align-items:center;gap:8px}
.call-icon{width:26px;height:26px;border-radius:50%;background:var(--yellow);display:flex;align-items:center;justify-content:center}
.call-text{font-size:8px;line-height:1.2}
.call-text strong{display:block;font-size:15px;color:var(--purple)}
.hero{position:absolute;top:56px;left:0;width:813px;height:340px;overflow:hidden;background:#d9d6d3}
.hero-photo{position:absolute;inset:0;background:linear-gradient(100deg,#8c7a6a 0%,#c7b8a8 30%,#e4e0dc 55%,#cfcac5 100%)}
.hero-stripe{position:absolute;inset:0}
.hero-caption{position:absolute;left:665px;top:258px;width:130px;background:var(--purple);color:var(--white);font-size:10px;font-weight:600;padding:8px 9px;line-height:1.4;z-index:2}
.hero-arrow{position:absolute;top:150px;width:18px;height:26px;background:rgba(0,0,0,.35);display:flex;align-items:center;justify-content:center}
.hero-arrow.left{left:0}.hero-arrow.right{right:0}
.cards-band{position:absolute;top:396px;left:0;width:813px;height:168px;background:var(--grey-light)}
.cards{position:absolute;top:352px;left:150px;display:flex;gap:10px;z-index:2}
.card{width:160px;background:var(--white);box-shadow:0 2px 6px rgba(0,0,0,.2)}
.card-title{background:var(--yellow);color:var(--grey-dark);font-weight:600;font-size:12px;text-align:center;padding:6px 0}
.card-photo{height:166px;position:relative}
.card-text{position:absolute;left:8px;right:8px;bottom:8px;background:rgba(107,68,155,.88);color:var(--white);font-size:7px;line-height:1.4;padding:6px}
.welcome{position:absolute;top:582px;left:0;width:813px;text-align:center;padding:0 90px}
.welcome h2{font-size:17px;font-weight:600;color:var(--grey-dark)}
.rule{width:60px;height:3px;background:var(--yellow);margin:6px auto 14px}
.welcome p{font-size:8px;line-height:1.6}
.welcome .cta{margin-top:10px;font-weight:700;color:var(--grey-dark)}
.accred{position:absolute;top:730px;left:0;width:813px;height:205px;background:var(--grey-dark);overflow:hidden}
.accred h2{position:relative;color:var(--white);text-align:center;font-weight:600;font-size:20px;margin-top:26px}
.accred .rule{position:relative}
.badges{position:relative;display:flex;justify-content:center;gap:14px;margin-top:30px}
.badge{width:132px;height:44px;background:var(--white);display:flex;align-items:center;justify-content:center}
.badge span{width:90px;height:22px;border-radius:3px}
.footer{position:absolute;top:935px;left:0;width:813px;height:245px;background:var(--grey-light);display:flex;padding:26px 52px 0;gap:40px;font-size:9px;line-height:1.7}
.footer h3{color:var(--purple);font-size:11px;font-weight:700;margin-bottom:8px}
.footer ul{list-style:none}
.footer p{margin-bottom:4px}
.col-links{width:110px}
.col-contact{width:190px}
.col-hours{width:150px}
.foot-logo{margin-left:auto;margin-top:30px;display:flex;align-items:flex-start;gap:6px}
.foot-logo .logo-mark{background:var(--purple);margin-top:3px}
.foot-logo .logo-name{color:var(--purple)}
.row{display:flex;gap:6px;align-items:flex-start;margin-bottom:4px}
.row svg{margin-top:3px;flex:none}
.copyright{position:absolute;top:1180px;left:0;width:813px;height:20px;background:var(--purple);color:var(--white);font-size:7px;padding:5px 52px}
</style>
</head>
<body>
<header class="header">
  <div class="logo"><span class="logo-mark"></span><span class="logo-name">Brambleridge Podiatry</span></div>
  <nav class="nav"><a class="active" href="#">Home</a><a href="#">About Us</a><a href="#">Services</a><a href="#">Contact</a></nav>
  <div class="call">
    <div class="call-icon"><svg width="12" height="12" viewBox="0 0 24 24"><path fill="#fff" d="M6.6 10.8a15 15 0 0 0 6.6 6.6l2.2-2.2c.3-.3.7-.4 1-.2 1.1.4 2.3.6 3.6.6.6 0 1 .4 1 1V20c0 .6-.4 1-1 1A17 17 0 0 1 3 4c0-.6.4-1 1-1h3.5c.6 0 1 .4 1 1 0 1.3.2 2.5.6 3.6.1.3 0 .7-.2 1z"/></svg></div>
    <div class="call-text">Call us Today<strong>1300 482 907</strong></div>
  </div>
</header>

<section class="hero">
  <div class="hero-photo" role="img" aria-label="Runner sprinting beside a close-up of hands massaging a sore ankle"></div>
  <svg class="hero-stripe" width="813" height="340" viewBox="0 0 813 340"><polygon points="690,0 813,0 813,90 560,340 420,340" fill="#f7c51e"/><polygon points="813,140 813,340 640,340" fill="#f7c51e" opacity=".9"/></svg>
  <div class="hero-caption">Brambleridge Podiatry Is A Podiatry Clinic In The Heart Of Ashford Vale Centre</div>
  <div class="hero-arrow left"><svg width="8" height="10"><path d="M7 0 1 5l6 5" stroke="#fff" fill="none" stroke-width="2"/></svg></div>
  <div class="hero-arrow right"><svg width="8" height="10"><path d="M1 0l6 5-6 5" stroke="#fff" fill="none" stroke-width="2"/></svg></div>
</section>

<div class="cards-band"><svg width="813" height="168"><polygon points="560,0 640,0 813,0 813,168 470,168" fill="#f7c51e"/><polygon points="0,0 813,0 813,0 0,0" fill="none"/></svg></div>

<div class="cards">
  <article class="card"><div class="card-title">Sports Injuries</div>
    <div class="card-photo" role="img" aria-label="Athlete holding an injured knee" style="background:linear-gradient(135deg,#b79d86,#6f6a75)"><div class="card-text">Sprains, strains and running pain assessed and treated so you can return to training sooner.</div></div></article>
  <article class="card"><div class="card-title">Orthotic Therapy</div>
    <div class="card-photo" role="img" aria-label="Custom orthotic insoles on a table" style="background:linear-gradient(135deg,#c9c2bb,#7d7a8a)"><div class="card-text">Custom insoles moulded to your feet to ease pain and improve posture at work and play.</div></div></article>
  <article class="card"><div class="card-title">Nail Surgery</div>
    <div class="card-photo" role="img" aria-label="Podiatrist treating a patient's toenail" style="background:linear-gradient(135deg,#d8c3b2,#857b8c)"><div class="card-text">Gentle treatment for ingrown and painful toenails under local anaesthetic in our clinic.</div></div></article>
</div>

<section class="welcome">
  <h2>Welcome to Brambleridge Podiatry</h2>
  <div class="rule"></div>
  <p>Brambleridge Podiatry is a Podiatry clinic in the heart of Ashford Vale Centre. We are located between Larch &amp; Wendell Streets in the Ashford Business Centre near the central station. Our podiatrists are fully qualified health professionals who are able to diagnose, treat, manage or help to prevent all medical conditions that affect the feet and lower limb. We provide General Podiatry Treatment and some Specialised Services in relation to various foot conditions, including Sports Injuries, Orthotic Therapy and Nail Surgery.</p>
  <p class="cta">For Appointments or Enquiries please<br>call us on 1300 482 907 or email : info@brambleridgepodiatry.net</p>
</section>

<section class="accred">
  <svg style="position:absolute;left:0;top:0" width="813" height="205"><polygon points="0,60 260,205 0,205" fill="#6b449b"/></svg>
  <h2>Our Accreditations</h2>
  <div class="rule"></div>
  <div class="badges">
    <div class="badge"><span style="background:#2d3a8c"></span></div>
    <div class="badge"><span style="background:#1f5fa8"></span></div>
    <div class="badge"><span style="background:#e23b3b"></span></div>
    <div class="badge"><span style="background:#2fa84f"></span></div>
  </div>
</section>

<footer class="footer">
  <div class="col-links"><h3>Quick Links</h3>
    <ul><li>Consulting</li><li>Inspections</li><li>Training</li><li>General Contracting</li><li>Clients</li><li>Contact Us</li></ul></div>
  <div class="col-contact"><h3>Contact Details</h3>
    <div class="row"><svg width="8" height="10" viewBox="0 0 8 10"><path d="M4 0a3 3 0 0 1 3 3c0 2.5-3 7-3 7S1 5.5 1 3a3 3 0 0 1 3-3z" fill="#6b449b"/></svg><span>Suite 14 / 260 Larch Street,<br>Ashford Vale, 3090</span></div>
    <div class="row"><svg width="8" height="10" viewBox="0 0 24 24"><path fill="#6b449b" d="M6.6 10.8a15 15 0 0 0 6.6 6.6l2.2-2.2c.3-.3.7-.4 1-.2 1.1.4 2.3.6 3.6.6.6 0 1 .4 1 1V20c0 .6-.4 1-1 1A17 17 0 0 1 3 4c0-.6.4-1 1-1h3.5c.6 0 1 .4 1 1 0 1.3.2 2.5.6 3.6.1.3 0 .7-.2 1z"/></svg><span>1300 482 907</span></div>
    <div class="row"><svg width="8" height="8" viewBox="0 0 10 8"><rect width="10" height="8" fill="#6b449b"/><path d="M0 0l5 4 5-4" stroke="#fff" fill="none"/></svg><span>info@brambleridgepodiatry.net</span></div></div>
  <div class="col-hours"><h3>Hours of Operation</h3>
    <p>Monday to Friday<br>10:00am to 8:00pm</p><p>Saturday<br>10:00am to 6:00pm</p><p>Sunday<br>By Appointment Only</p></div>
  <div class="foot-logo"><span class="logo-mark"></span><span class="logo-name">Brambleridge Podiatry</span></div>
</footer>
<div class="copyright">Copyright © 2016 Brambleridge Podiatry. All Rights Reserved.</div>
</body>
</html>
```